Teeth Whitening Clinic Website Redesign - Social Proof Theme

NEW TEETH SITEREVAMP CURRENT WEBSITE:WWW.SANDIEGOSTEETHWHITENING.COMTHEME:SOCIAL PROOF/5 STAR REVIEWS/TESTIMONIALS THEME:https://maps.example.net/QxRvPLoKzN84 I want a testimonial themed, social proof themed website so customers will be sold by testimonials all over the website….I like a nice clean simple site but with all important factors standing out like CALLS TO ACTIONS, for example the $99 special link in header on original design. Also, testimonials throughout the website placed methodically as not to be FORCED and CLUTTEREDKeep all same exact content for all pages and elements of current design. All buttons, calls to action, navigation, etc. Please do not leave anything out from current design. SPECIAL INSTRUCTIONS for banner image:I want to use actual customer photos inside the banner image in a way that really pops and grabs attention. Please grab some customer photos from my PG Account, fk or rateway account: Also, I want to integrate 5 star rateway logo, friendbook review 5 stars icon, searchly business page 5 stars icon, etc. on the banner as well to show social proof as much as possible. Actual customer photos to be used throughout website:https://www.photogram.example/brightharborsmilestudioplace/ https://www.friendbook.com/SDTeethWhitening/https://www.reviewhub.example/biz/bright-harbor-smile-studio-place-bright-harbor-5 Reviews:https://www.reviewhub.example/biz/bright-harbor-smile-studio-place-bright-harbor-5 https://www.friendbook.com/pg/SDTeethWhitening/reviews/?ref=page_internalhttps://goo.gl/maps/TmJcABLAJwC2 Please do home page first to come up with theme then after approval home page we can move forward additional pages.

Target Market(s)

PEOPLE THAT CARE ABOUT DENTAL HYGEINE AND OR CARE ABOUT THEIR TEETH SMILE

Industry/Entity Type

Dental Clinic

Number of Pages Required

5+ page

Colors

Designer to choose colors to be used in the design.

Requirements
Must have
• NEW TEETH SITE
• REVAMP CURRENT WEBSITE:
• WWW.BRIGHTHARBORSMILESTUDIO.EXAMPLE
• THEME:
• SOCIAL PROOF/5 STAR REVIEWS/TESTIMONIALS THEME:
• https://maps.example.net/QxRvPLoKzN84
• I want a testimonial themed, social proof themed website so customers will be sold by testimonials all over the website….I like a nice clean simple site but with all important factors standing out like CALLS TO ACTIONS, for example the $99 special link in header on original design. Also, testimonials throughout the website placed methodically as not to be FORCED and CLUTTERED
• Keep all same exact content for all pages and elements of current design. All buttons, calls to action, navigation, etc. Please do not leave anything out from current design.
• SPECIAL INSTRUCTIONS for banner image:
• I want to use actual customer photos inside the banner image in a way that really pops and grabs attention. Please grab some customer photos from my PG Account, fk or rateway account:
• Also, I want to integrate 5 star rateway logo, friendbook review 5 stars icon, searchly business page 5 stars icon, etc. on the banner as well to show social proof as much as possible.
• Actual customer photos to be used throughout website:
• https://www.photogram.example/brightharborsmilestudioplace/
• https://www.friendbook.example/BHSmileStudio/
• https://www.reviewhub.example/biz/bright-harbor-smile-studio-place-bright-harbor-5
• Reviews:
• https://www.friendbook.example/pg/BHSmileStudio/reviews/?ref=page_internal
• Please do home page first to come up with theme then after approval home page we can move forward additional pages.
Nice to have
• NEW TEETH SITE
• REVAMP CURRENT WEBSITE:
• THEME:
• Reviews:
Should not have
• NEW TEETH SITE
• REVAMP CURRENT WEBSITE:
• THEME:
• Reviews:

```html
<!DOCTYPE html>
<html lang="en">
<head>
<meta charset="utf-8">
<title>Bright Harbor's Smile Studio</title>
<link href="https://fonts.googleapis.com/css2?family=Lato:wght@300;400;700&family=Marcellus+SC&display=swap" rel="stylesheet">
<style>
:root{
  --blue:#12a3cf;
  --blue-dark:#0c8db5;
  --ink:#333;
  --grey:#4b4b4b;
  --muted:#8a8a8a;
  --line:#e3e3e3;
  --panel:#f7f7f7;
  --star:#f5b301;
}
*{box-sizing:border-box;margin:0;padding:0}
html,body{width:1200px;height:3910px;overflow:hidden;background:#fff}
body{position:relative;font-family:'Lato',sans-serif;color:var(--ink)}
.abs{position:absolute}
.serif{font-family:'Marcellus SC',serif}
.accent{color:var(--blue)}

.topbar{left:0;top:0;width:1200px;height:34px;background:var(--blue);color:#fff;font-size:11px;display:flex;align-items:center;padding:0 112px}
.topbar .social{margin-left:auto;display:flex;gap:6px;font-size:10px;font-weight:700}

.logo{left:110px;top:52px;display:flex;align-items:center;gap:10px}
.logo .mark{width:56px;height:56px;border-radius:50%;border:2px solid #c7d3da}
.logo .name{font-family:'Marcellus SC',serif;font-size:25px;color:var(--grey);line-height:1}
.logo .sub{font-family:'Marcellus SC',serif;font-size:13px;color:var(--blue);margin-top:3px}
.contact-item{display:flex;align-items:center;gap:12px;font-size:11px;color:#555;line-height:21px;top:62px}
.ring{width:42px;height:42px;border-radius:50%;border:1px solid var(--line);display:flex;align-items:center;justify-content:center;color:var(--blue);font-weight:700;font-size:18px}
.phone-num{font-size:17px;color:#333}
.rule{left:0;width:1200px;height:1px;background:var(--line)}

.nav{left:110px;top:137px;height:68px;display:flex;align-items:center;gap:26px;font-size:14px;color:#333}
.btn-book{left:898px;top:155px;width:190px;height:34px;background:var(--grey);color:#fff;font-size:12.5px;display:flex;align-items:center;justify-content:center;gap:6px}

.tile{width:300px;height:268px;overflow:hidden}
.photo{background:linear-gradient(135deg,#b9a49c,#6a5a62 60%,#3d3442)}
.photo.light{background:linear-gradient(135deg,#e8e2de,#c9b6ad 55%,#9c8a8c)}
.badge-tile{background:linear-gradient(135deg,#f2f2f2,#e2e2e2);display:flex;flex-direction:column;align-items:center;justify-content:center;gap:12px}
.badge-name{font-family:'Lato',sans-serif;font-weight:700;font-size:40px;color:var(--grey);display:flex;align-items:center;gap:10px;line-height:1}
.badge-name .sq{width:28px;height:28px;background:var(--blue)}
.badge-sub{font-size:14px;color:#555;margin-top:-6px}
.cta-tile{background:var(--blue);color:#fff;padding:40px 28px}
.cta-tile .l1{font-size:24px}
.cta-tile .l2{font-size:37px;margin:4px 0 6px}
.cta-tile .l3{font-size:22px}
.cta-tile .btns{display:flex;gap:10px;margin-top:36px}
.cta-tile .btns span{height:36px;padding:0 18px;display:flex;align-items:center;font-size:12.5px}
.b-white{background:#fff;color:var(--blue)}
.b-dark{background:var(--grey);color:#fff}

.about-title{left:110px;top:865px;font-size:30px;line-height:46px;color:#333;font-weight:400}
.about-lead{left:110px;top:962px;font-size:21px;color:#222}
.about-copy{left:110px;top:1010px;width:420px;font-size:12px;line-height:34.5px;color:var(--muted)}
.video{left:589px;top:847px;width:499px;height:379px;background:linear-gradient(135deg,#d8d8d8,#9d9aa0 55%,#5c4a55)}
.play{left:809px;top:1007px;width:60px;height:60px;border-radius:50%;border:3px solid #fff}

.section-title{width:1200px;left:0;text-align:center;font-size:34px;color:#333;font-weight:400}
.ctable{top:2222px;width:228px;height:246px;background:var(--panel);border:1px solid var(--line)}
.ctable h4{height:44px;background:var(--grey);color:#fff;font-weight:400;font-size:13.5px;display:flex;align-items:center;padding-left:24px;margin:-1px -1px 0}
.ctable.hl h4{background:var(--blue)}
.ctable ul{list-style:none;padding:18px 0 0 24px;font-size:12.5px;color:#555}
.ctable li{height:33.5px;display:flex;align-items:center}
.ctable li::before{content:"»";margin-right:20px;color:#555}
.arrow-btn{width:40px;height:40px;border-radius:50%;border:1.5px solid var(--blue);display:flex;align-items:center;justify-content:center}

.how-photo{left:0;top:2594px;width:600px;height:457px;background:linear-gradient(135deg,#d5d3d6,#8c7c86 50%,#4d3f4d)}
.how-box{left:561px;top:2574px;width:525px;height:496px;border:3px solid var(--blue)}
.how-title{left:652px;top:2618px;font-size:36px;color:#333;font-weight:400}
.how-copy{left:652px;top:2682px;width:395px;font-size:12px;line-height:36px;color:var(--muted)}
.btn-more{left:652px;top:2969px;width:127px;height:50px;border-radius:25px;background:var(--blue);color:#fff;font-size:12.5px;display:flex;align-items:center;justify-content:center}

.testi{top:3292px;width:320px;display:flex;gap:22px}
.avatar{flex:none;width:76px;height:76px;border-radius:50%;border:4px solid #eee;background:linear-gradient(135deg,#d8c6b4,#8e7a6c)}
.quote{font-size:11.5px;line-height:24px;color:var(--muted);font-style:italic}
.quote b{color:var(--blue);font-size:16px;margin-right:8px}
.who{font-size:11px;color:#222;margin-top:12px;line-height:16px}
.who small{display:block;font-size:10.5px}

.footer{left:0;top:3583px;width:1200px;height:327px;background:var(--grey);border-top:4px solid var(--blue);color:#fff}
.f-social{position:absolute;top:68px;left:468px;display:flex;gap:15px}
.f-social span{width:55px;height:55px;border-radius:50%;border:2px solid #fff;display:flex;align-items:center;justify-content:center;font-size:13px;font-weight:700}
.f-nav{position:absolute;top:152px;width:100%;display:flex;justify-content:center;gap:26px;font-size:13.5px}
.f-contact{position:absolute;top:198px;width:100%;text-align:center;font-size:12.5px}
.f-copy{position:absolute;top:238px;width:100%;text-align:center;font-size:12.5px}
</style>
</head>
<body>

<svg width="0" height="0" style="position:absolute">
  <defs>
    <path id="star" d="M9 0l2.6 5.6 6 .6-4.5 4.1 1.3 6L9 13.2 3.6 16.3l1.3-6L.4 6.2l6-.6z"/>
  </defs>
</svg>

<div class="abs topbar">
  <span>◷ Clinic Open: Mon-Fri 9:15 am to 5:30 pm Sat 10am to 2pm &nbsp;|&nbsp; ✎ Book Appointments: Mon-Fri 830 am to 5 pm</span>
  <span class="social"><span>fk</span><span>tw</span><span>pg</span></span>
</div>

<div class="abs logo">
  <div class="mark"></div>
  <div><div class="name">Bright Harbor's</div><div class="sub">Smile Studio Whitening Center</div></div>
</div>
<div class="abs contact-item" style="left:443px;top:62px">
  <div class="ring">$</div><div>Click Here to Get Our $99 Teeth<br>Whiting Deal (Reg: $378)</div>
</div>
<div class="abs contact-item" style="left:667px;top:62px">
  <div class="ring"><svg width="14" height="18" viewBox="0 0 14 18"><path d="M7 0a7 7 0 0 0-7 7c0 5 7 11 7 11s7-6 7-11a7 7 0 0 0-7-7zm0 10a3 3 0 1 1 0-6 3 3 0 0 1 0 6z" fill="#12a3cf"/></svg></div>
  <div>4410 Harbor Crest Rd. #205<br>Bayview, CA 90000</div>
</div>
<div class="abs contact-item" style="left:906px;top:62px">
  <div class="ring"><svg width="16" height="16" viewBox="0 0 24 24"><path d="M6.6 10.8a15 15 0 0 0 6.6 6.6l2.2-2.2a1 1 0 0 1 1-.25 11.4 11.4 0 0 0 3.6.57 1 1 0 0 1 1 1V20a1 1 0 0 1-1 1A17 17 0 0 1 3 4a1 1 0 0 1 1-1h3.5a1 1 0 0 1 1 1c0 1.25.2 2.45.57 3.57a1 1 0 0 1-.25 1z" fill="#12a3cf"/></svg></div>
  <div class="phone-num">1-555-014-2273</div>
</div>
<div class="abs rule" style="top:137px"></div>

<nav class="abs nav">
  <span>Home</span><span>Our Process</span><span>Photos</span><span>Free Treatments</span><span>Testimonials</span><span>Blog</span><span>FAQ</span><span>Contact</span><span>Gift Certificates</span>
</nav>
<div class="abs btn-book">✎ Book Appointment Online</div>
<div class="abs rule" style="top:205px"></div>

<!-- hero grid -->
<div class="abs tile photo" style="left:0;top:205px" role="img" aria-label="Customer photo: smiling clients holding review signs"></div>
<div class="abs tile badge-tile" style="left:300px;top:205px">
  <div class="badge-name">rateway</div>
  <svg width="150" height="28" viewBox="0 0 150 28"><g fill="#f5b301" transform="scale(1.5)"><use href="#star"/><use href="#star" x="20"/><use href="#star" x="40"/><use href="#star" x="60"/><use href="#star" x="80"/></g></svg>
</div>
<div class="abs tile photo" style="left:600px;top:205px" role="img" aria-label="Customer photo: happy client after treatment"></div>
<div class="abs tile photo light" style="left:900px;top:205px" role="img" aria-label="Customer photo: smiling clients with sign"></div>

<div class="abs tile badge-tile" style="left:0;top:472px">
  <div class="badge-name"><span class="sq"></span><span>searchly</span></div>
  <div class="badge-sub">My Business</div>
</div>
<div class="abs tile photo light" style="left:300px;top:472px" role="img" aria-label="Customer photo: two smiling clients"></div>
<div class="abs tile cta-tile serif" style="left:600px;top:472px">
  <div class="l1">Get That White</div>
  <div class="l2">Smile You've</div>
  <div class="l3">Always Wanted</div>
  <div class="btns" style="font-family:'Lato',sans-serif"><span class="b-white">Book Online</span><span class="b-dark">Contact us</span></div>
</div>
<div class="abs tile badge-tile" style="left:900px;top:472px">
  <div class="badge-name">friendbook</div>
  <svg width="150" height="28" viewBox="0 0 150 28"><g fill="#f5b301" transform="scale(1.5)"><use href="#star"/><use href="#star" x="20"/><use href="#star" x="40"/><use href="#star" x="60"/><use href="#star" x="80"/></g></svg>
</div>

<!-- about -->
<h2 class="abs about-title serif">About Bright Harbor's Smile<br><span class="accent">Studio Whitening Center</span></h2>
<p class="abs about-lead">The best price, service and results.</p>
<p class="abs about-copy">Bright Harbor's Smile Studio features state-of-the-art technologies that are safe, industry-unique and very cost-effective. Our teeth whitening system utilizes the latest blue light whitening technology. Our Blue Light Systems are calibrated precisely for optimal activation of our exclusive hydrogen peroxide based whitening solution which is manufactured in a FDA registered facility in the USA.</p>
<div class="abs video" role="img" aria-label="Video still: clinic staff member speaking at front desk"></div>
<div class="abs play"><svg width="54" height="54" viewBox="0 0 54 54"><path d="M21 16l17 11-17 11z" fill="#fff"/></svg></div>

<!-- why choose us -->
<svg class="abs" style="left:0;top:1347px" width="1200" height="720" viewBox="0 0 1200 720">
  <defs>
    <linearGradient id="toothArea" x1="0" x2="1"><stop offset="0" stop-color="#c9cdd1"/><stop offset=".5" stop-color="#eef1f3"/><stop offset="1" stop-color="#bfe6f3"/></linearGradient>
  </defs>
  <rect width="1200" height="607" fill="#12a3cf"/>
  <text x="600" y="124" text-anchor="middle" font-family="Marcellus SC, serif" font-size="36" fill="#fff">WHY CHOOSE US</text>
  <circle cx="592" cy="610" r="226" fill="#fff"/>
  <circle cx="592" cy="610" r="200" fill="none" stroke="#12a3cf" stroke-width="14"/>
  <rect x="0" y="607" width="1200" height="120" fill="#fff"/>
  <rect x="366" y="560" width="24" height="47" fill="#fff"/>
  <rect x="794" y="560" width="24" height="47" fill="#fff"/>
  <g stroke="#fff" stroke-width="2" stroke-dasharray="3 4" fill="none">
    <line x1="287" y1="498" x2="396" y2="536"/>
    <line x1="364" y1="364" x2="446" y2="454"/>
    <line x1="501" y1="291" x2="539" y2="408"/>
    <line x1="686" y1="287" x2="643" y2="408"/>
    <line x1="813" y1="358" x2="725" y2="452"/>
    <line x1="884" y1="496" x2="778" y2="528"/>
  </g>
  <g fill="#fff" stroke="#12a3cf" stroke-width="4">
    <circle cx="396" cy="536" r="8"/><circle cx="446" cy="454" r="8"/><circle cx="539" cy="408" r="8"/>
    <circle cx="643" cy="408" r="8"/><circle cx="725" cy="452" r="8"/><circle cx="778" cy="528" r="8"/>
  </g>
  <g fill="#12a3cf" stroke="#fff" stroke-width="3">
    <circle cx="287" cy="498" r="33"/><circle cx="364" cy="364" r="33"/><circle cx="501" cy="291" r="33"/>
    <circle cx="686" cy="287" r="33"/><circle cx="813" cy="358" r="33"/><circle cx="884" cy="496" r="33"/>
  </g>
  <g fill="none" stroke="#fff" stroke-width="2.5" stroke-linecap="round" stroke-linejoin="round">
    <path d="M287 482v32M296 488c-3-3-15-3-15 3s15 4 15 10-12 6-15 3"/>
    <path d="M350 374h28M352 370l8-9 6 5 10-10M371 356h5v5"/>
    <path d="M490 294h6v12h-6zM496 305h14a3 3 0 0 0 3-3l1-8a3 3 0 0 0-3-3h-8l1-6a3 3 0 0 0-6-1l-2 7"/>
    <circle cx="681" cy="290" r="6"/><circle cx="694" cy="281" r="4"/>
    <path d="M797 365v-16h18v16zM815 353h8l5 6v6h-13M801 368a3 3 0 1 0 .1 0M822 368a3 3 0 1 0 .1 0"/>
    <path d="M872 482h14M872 482v26h26v-14M882 500l3-9 14-14 6 6-14 14z"/>
  </g>
  <g font-family="Lato, sans-serif" font-size="19" fill="#fff">
    <text x="195" y="505">Price</text>
    <text x="252" y="364">Results</text>
    <text x="464" y="245">No Pain</text>
    <text x="655" y="240">Service</text>
    <text x="855" y="352">Convenience</text>
    <text x="928" y="488">Easy</text>
    <text x="928" y="517">Booking</text>
  </g>
  <circle cx="592" cy="578" r="110" fill="url(#toothArea)" role="img" aria-label="Illustration area: a tooth shown before and after whitening"/>
</svg>

<!-- compare us -->
<h2 class="abs section-title serif" style="top:2128px">Compare Us</h2>
<div class="abs arrow-btn" style="left:60px;top:2324px"><svg width="10" height="14" viewBox="0 0 10 14"><path d="M8 1L2 7l6 6" fill="none" stroke="#12a3cf" stroke-width="2"/></svg></div>
<div class="abs arrow-btn" style="left:1100px;top:2324px"><svg width="10" height="14" viewBox="0 0 10 14"><path d="M2 1l6 6-6 6" fill="none" stroke="#12a3cf" stroke-width="2"/></svg></div>
<div class="abs ctable" style="left:112px"><h4>FEATURES</h4><ul><li>Speed</li><li>Ease of Use</li><li>Cost</li><li>Availability</li><li>Pain</li></ul></div>
<div class="abs ctable hl" style="left:361px"><h4>LUMAPRO</h4><ul><li>1-2 Hours</li><li>Difficult / Dentist</li><li>$300 - $600</li><li>Limited Availability</li><li>Pain &amp; Sensitivity</li></ul></div>
<div class="abs ctable" style="left:611px"><h4>GLEAMSET</h4><ul><li>7-14 Days</li><li>Difficult / Dentist</li><li>$300 - $600</li><li>Limited Availability</li><li>Sensitivity</li></ul></div>
<div class="abs ctable" style="left:861px"><h4>HOME KITS</h4><ul><li>7-30 Days</li><li>Difficult</li><li>$50 - $150</li><li>Store Purchase</li><li>Sensitivity</li></ul></div>

<!-- how it works -->
<div class="abs how-box"></div>
<div class="abs how-photo" role="img" aria-label="Photo: clinic team with a happy client holding review signs"></div>
<h2 class="abs how-title serif">How It <span class="accent">Works</span></h2>
<p class="abs how-copy">We have a very effective teeth whitening treatment that is guaranteed to get you quick results in about 1 hour. To start the treatment you'll apply a Hydrogen Peroxide based whitening agent to your teeth. We then place our cold blue light directly in front of your exposed teeth for 15 minutes per treatment. The lighting systems we use activate the whitening agent and thats what accelerates the whitening process, giving you whiter teeth in less than an hour.</p>
<div class="abs btn-more">READ MORE</div>

<!-- testimonials -->
<h2 class="abs section-title serif" style="top:3188px">Client <span class="accent">Testimonials</span></h2>
<div class="abs arrow-btn" style="left:30px;top:3386px"><svg width="10" height="14" viewBox="0 0 10 14"><path d="M8 1L2 7l6 6" fill="none" stroke="#12a3cf" stroke-width="2"/></svg></div>
<div class="abs arrow-btn" style="left:1130px;top:3386px"><svg width="10" height="14" viewBox="0 0 10 14"><path d="M2 1l6 6-6 6" fill="none" stroke="#12a3cf" stroke-width="2"/></svg></div>

<div class="abs testi" style="left:94px">
  <div class="avatar" role="img" aria-label="Client photo"></div>
  <div>
    <p class="quote"><b>❝</b>The staff is really friendly and welcoming and Dana did such a good job with my smile!</p>
    <p class="who">MARISA HOLLEN<small>Financial Services Professional</small></p>
    <svg width="110" height="18" viewBox="0 0 110 18" style="margin-top:16px"><g fill="#f5b301"><use href="#star"/><use href="#star" x="22"/><use href="#star" x="44"/><use href="#star" x="66"/></g><use href="#star" x="88" fill="none" stroke="#f5b301"/></svg>
  </div>
</div>
<div class="abs testi" style="left:444px">
  <div class="avatar" role="img" aria-label="Client photo" style="background:linear-gradient(135deg,#9bc25a,#5b7c2a)"></div>
  <div>
    <p class="quote"><b>❝</b>Seriously, Carla worked her magic hands on my teeth as I played the part of the magician assistant.</p>
    <p class="who">TALIA R. BRENNAN<small>National Urban Fellow at the Riverton</small></p>
    <svg width="110" height="18" viewBox="0 0 110 18" style="margin-top:16px"><g fill="#f5b301"><use href="#star"/><use href="#star" x="22"/><use href="#star" x="44"/><use href="#star" x="66"/></g><use href="#star" x="88" fill="none" stroke="#f5b301"/><path d="M97 0v13.2l-5.4 3.1 1.3-6-4.5-4.1 6-.6z" fill="#f5b301"/></svg>
  </div>
</div>
<div class="abs testi" style="left:792px">
  <div class="avatar" role="img" aria-label="Client photo" style="background:linear-gradient(135deg,#f0d7b8,#c59a72)"></div>
  <div>
    <p class="quote"><b>❝</b>I also appreciated that they took the Delgado explain all the instructions and didn't mind me asking.</p>
    <p class="who">JOANNE PETTIS<small>Creative Strategist | Entrepreneur &amp; Upcoming</small></p>
    <svg width="110" height="18" viewBox="0 0 110 18" style="margin-top:16px"><g fill="#f5b301"><use href="#star"/><use href="#star" x="22"/><use href="#star" x="44"/><use href="#star" x="66"/></g><use href="#star" x="88" fill="none" stroke="#f5b301"/></svg>
  </div>
</div>

<!-- footer -->
<footer class="abs footer">
  <div class="f-social"><span>fk</span><span>vt</span><span>lw</span><span>pb</span></div>
  <div class="f-nav"><span>HOME</span><span>OUR PROCESS</span><span>PHOTOS</span><span>FREE TREATMENTS</span><span>TESTIMONIALS</span><span>BLOG</span><span>FAQ</span><span>CONTACT</span><span>GIFT CERTIFICATES</span></div>
  <div class="f-contact">⌖ &nbsp;4410 Harbor Crest Rd. #205 Bayview, CA 90000 &nbsp;| &nbsp;☏ &nbsp;1-555-014-2273 &nbsp;| &nbsp;✉ &nbsp;Email: info@brightharbor.example</div>
  <div class="f-copy">© Copyright 2018 Bright Harbor.All Rights Reserved</div>
</footer>

</body>
</html>
```